Set up small scale company website

We need a website set up for our educational consultancy - Vexmore Education. We like the following site and want something similar www.plindarhub.co.uk We can provide the copy and images but need the following:- setting up the overall theme and design - to our requirements on colours and forma- Approximately 4 pages of services offered and with an index pageEtct (yellow and green)And the following pages - as well as a home page:- A contact page linked to our email addresses and registered business address 17 Wexbury Lane, Dunmere, Kestshire, CO14 8PN- About Us page - An index of services page that links to between 4-6 pages outlining services- A News page that links to updates of latest services, events and activities - easily updated by usOn the homepage we'd like links to chirpnet and WorkLoop feeds and links to our other blogs and websites
Target Market(s)
Schools, local authoroties and multi-academy trusts
Logo Text
Vexmore Education
Coding
Coded - Design and coding required
Number of Pages Required
5+ page
Font styles to use
Requirements
Should not have
- No tacky pictures of mortar boards or chalk boards etc.

```html
<!DOCTYPE html>
<html lang="en">
<head>
<meta charset="utf-8">
<title>Vexmore Education</title>
<link rel="stylesheet" href="https://fonts.googleapis.com/css2?family=Lato:wght@400;700;900&family=Roboto:wght@400;500;700&display=swap">
<style>
:root{
  --green:#8cc63f;
  --green-dark:#78b22e;
  --green-soft:#d9e9ab;
  --green-pale:#f6f9ea;
  --ink:#151515;
  --text:#555;
  --link:#2b9fd9;
  --work:#1f5fa0;
  --bar:#1e1e1e;
  --grey-band:#f1f1f1;
  --white:#fff;
}
*{box-sizing:border-box;margin:0;padding:0}
html,body{width:1200px;height:2439px;overflow:hidden}
body{position:relative;background:var(--white);font-family:'Roboto',sans-serif;color:var(--text)}
.abs{position:absolute}

/* top bar */
.topbar{left:0;top:0;width:1200px;height:41px;background:var(--bar);color:#eee;font-size:14px}
.topbar .follow{left:111px;top:0;height:41px;display:flex;align-items:center;gap:12px;font-weight:500}
.topbar .follow .net{display:flex;align-items:center;gap:5px;font-weight:400;font-size:12px}
.topbar .follow .net i{width:8px;height:8px;border-radius:50%;background:#eee}
.topbar .contact{right:112px;top:0;height:41px;display:flex;align-items:center;gap:22px;font-size:13.5px}
.topbar svg{vertical-align:-2px;margin-right:6px}

/* header */
.header{left:0;top:41px;width:1200px;height:122px;background:var(--white)}
.brand{left:111px;top:40px;display:flex;align-items:center;gap:14px;font-family:'Lato',sans-serif;font-weight:900;font-size:33px;color:var(--ink);letter-spacing:.3px}
.brand .dot{width:30px;height:30px;border-radius:50%;background:var(--green)}
.nav{left:592px;top:66px;display:flex;gap:36px;font-weight:500;font-size:16.5px;color:var(--ink);text-transform:uppercase}
.nav .active{position:relative}
.nav .active::before{content:"";position:absolute;left:50%;top:-24px;width:14px;height:14px;margin-left:-7px;border-radius:50%;background:var(--green)}

/* hero */
.hero{left:0;top:163px;width:1200px;height:491px;background:linear-gradient(180deg,#d8c9b2 0%,#b89a80 45%,#8a7566 100%)}
.hero-caption{left:563px;top:418px;width:637px;height:171px;background:rgba(140,198,63,.92);padding:24px 50px;color:var(--white)}
.hero-caption h1{font-family:'Lato',sans-serif;font-weight:900;font-size:47px;line-height:1.1}
.hero-caption p{font-family:'Lato',sans-serif;font-weight:700;font-size:18.5px;line-height:1.6;margin-top:10px;width:470px}

/* welcome */
.welcome-title{left:111px;top:740px;font-family:'Lato',sans-serif;font-weight:900;font-size:44px;color:var(--ink)}
.welcome-copy{left:111px;top:829px;width:602px;font-size:15.5px;line-height:31px;color:var(--text);text-align:justify}
.btn-more{left:111px;top:1073px;width:249px;height:50px;border:2px solid #ddd;border-radius:25px;display:flex;align-items:center;justify-content:center;gap:6px;font-family:'Lato',sans-serif;font-weight:900;font-size:14.5px;color:var(--green-dark);text-transform:uppercase}

/* services */
.services{left:821px;top:751px;width:266px;border:2px solid #eef3dc;background:var(--white)}
.services h3{background:var(--green);color:var(--white);font-family:'Lato',sans-serif;font-weight:700;font-size:21px;height:49px;line-height:49px;padding-left:20px}
.services li{list-style:none;height:54px;line-height:54px;padding-left:20px;font-family:'Lato',sans-serif;font-size:17px;color:#555}
.services li:nth-child(odd){background:var(--green-pale)}
.services li:nth-child(even){background:var(--green-soft)}

/* social feeds */
.wave{left:0;top:1200px;width:1200px;height:580px}
.section-title{left:0;width:1200px;text-align:center;font-family:'Lato',sans-serif;font-weight:900;font-size:42px;color:var(--ink)}
.feed{top:1413px;width:216px;height:272px;background:var(--white);box-shadow:0 1px 4px rgba(0,0,0,.16);padding:20px 18px}
.feed p{font-size:14px;line-height:26px;color:#444;width:172px}
.feed .at,.feed .url{color:var(--link)}
.feed .url.alt{color:var(--green-dark)}
.feed hr{border:0;border-top:2px solid #ddd;margin:16px 0 12px}
.feed .by{display:flex;align-items:center;gap:12px}
.feed .by .badge{width:34px;height:34px;border-radius:50%;background:var(--link);flex:none}
.feed .by .badge.work{background:var(--work)}
.feed .by strong{display:block;font-weight:400;font-size:15px;color:#555}
.feed .by small{font-size:10.5px;color:#555}

/* blog */
.blog-band{left:0;top:1777px;width:1200px;height:495px;background:linear-gradient(180deg,#f7f7f5,#efefec)}
.post-img{top:1981px;width:192px;height:184px;border-right:2px solid var(--green);border-bottom:2px solid var(--green)}
.date{top:1981px;width:40px;height:42px;background:var(--green);color:var(--white);text-align:center;font-family:'Lato',sans-serif;line-height:1}
.date span{display:block;font-size:13px;padding-top:4px}
.date b{display:block;font-size:23px;font-weight:900}
.post{top:1978px;width:250px}
.post h4{font-weight:700;font-size:18.5px;line-height:30px;color:var(--ink)}
.post p{font-size:14px;line-height:27px;color:#666;margin-top:12px}
.post a{display:block;margin-top:12px;font-family:'Lato',sans-serif;font-weight:900;font-size:15px;color:var(--green-dark);text-decoration:none}

/* footer */
.footer{left:0;top:2272px;width:1200px;height:167px;background:#1b1b1b;color:#eee;font-size:14px;line-height:28px}
.footer .addr{left:111px;top:53px}
.footer .copy{right:111px;top:53px;text-align:right}
.footer .socials{left:0;width:1200px;top:66px;display:flex;justify-content:center;gap:28px;font-size:14px}
.footer .socials span{display:flex;align-items:center;gap:8px}
.footer .socials i{width:10px;height:10px;border-radius:50%;background:#eee}
</style>
</head>
<body>

<div class="abs topbar">
  <div class="abs follow">Follow Us On: <span class="net"><i></i>Plazora</span><span class="net"><i></i>chirpnet</span></div>
  <div class="abs contact">
    <span><svg width="12" height="12" viewBox="0 0 24 24"><path fill="#eee" d="M6.6 10.8a15 15 0 0 0 6.6 6.6l2.2-2.2a1 1 0 0 1 1-.25 11 11 0 0 0 3.6.6 1 1 0 0 1 1 1V20a1 1 0 0 1-1 1A17 17 0 0 1 3 4a1 1 0 0 1 1-1h3.5a1 1 0 0 1 1 1 11 11 0 0 0 .6 3.6 1 1 0 0 1-.25 1z"/></svg>(+44) 1255 640 218</span>
    <span style="color:#888">|</span>
    <span><svg width="14" height="11" viewBox="0 0 24 18"><path fill="#eee" d="M0 0h24v2L12 10 0 2zM0 4l12 8 12-8v14H0z"/></svg>hello@vexmore-edu.co.uk</span>
  </div>
</div>

<header class="abs header">
  <div class="abs brand"><span class="dot"></span>Vexmore Education</div>
  <nav class="abs nav">
    <span class="active">Home</span><span>Services</span><span>News</span><span>About Us</span><span>Contact Us</span>
  </nav>
</header>

<section class="abs hero" role="img" aria-label="Photograph of smiling primary school pupils sitting at classroom desks"></section>
<div class="abs hero-caption">
  <h1>Vexmore Education</h1>
  <p>Lorem ipsum dolor sit amet consectetur adipiscing elit sed do eiusmod tempor.</p>
</div>

<h2 class="abs welcome-title">Welcome Vexmore Education</h2>
<p class="abs welcome-copy">Lorem ipsum dolor sit amet, consectetur adipiscing elit, sed do eiusmod tempor incididunt ut labore et dolore magna aliqua. Ut enim ad minim veniam, quis nostrud exercitation ullamco laboris nisi ut aliquip ex ea commodo consequat. Duis aute irure dolor in reprehenderit in voluptate velit esse cillum dolore eu fugiat nulla paria tur. Excepteur sint occaecat cupidatat non proident, sunt in culpa qui officia des erunt mollit anim id est laborum.</p>
<div class="abs btn-more">Read More About Us
  <svg width="14" height="14" viewBox="0 0 16 16"><circle cx="8" cy="8" r="8" fill="#78b22e"/><path d="M6 4l4 4-4 4" stroke="#fff" stroke-width="2" fill="none"/></svg>
</div>

<aside class="abs services">
  <h3>Vexmore Services</h3>
  <ul>
    <li>Education</li><li>Learning</li><li>Programming</li><li>Vexmore Engagements</li><li>Self-Awareness</li><li>Our Community</li>
  </ul>
</aside>

<svg class="abs wave" width="1200" height="580" viewBox="0 0 1200 580" aria-hidden="true">
  <path d="M0 40 C 300 -10 600 100 900 50 C 1050 25 1150 20 1200 30 L1200 580 L0 580 Z" fill="#f1f1f1"/>
</svg>

<h2 class="abs section-title" style="top:1322px">Social Feeds</h2>

<article class="abs feed" style="left:111px">
  <p>Lorem ipsum dolor it amet, consectetur adipiscing its sed do <span class="at">@eiusmod</span> tempor incididunt ut labore et dolore magna aliqua. <span class="url">https://lorenfield.org</span></p>
  <hr><div class="by"><span class="badge" aria-label="chirpnet"></span><div><strong>@vexmoreedu.</strong><small>5 hour ago</small></div></div>
</article>
<article class="abs feed" style="left:364px">
  <p>Lorem ipsum dolor it amet, consectetur adipiscing its sed do <span class="at">@eiusmod</span> tempor incididunt ut labore et dolore magna aliqua. <span class="url">https://lorenfield.org</span></p>
  <hr><div class="by"><span class="badge work" aria-label="WorkLoop"></span><div><strong>@vexmoreedu.</strong><small>5 hour ago</small></div></div>
</article>
<article class="abs feed" style="left:618px">
  <p>Lorem ipsum dolor it amet, consectetur adipiscing its sed do <span class="at">@eiusmod</span> tempor incididunt ut labore et dolore magna aliqua. <span class="url alt">https://lorenfield.org</span></p>
  <hr><div class="by"><span class="badge" aria-label="chirpnet"></span><div><strong>@vexmoreedu.</strong><small>5 hour ago</small></div></div>
</article>
<article class="abs feed" style="left:872px">
  <p>Lorem ipsum dolor it amet, consectetur adipiscing its sed do <span class="at">@eiusmod</span> tempor incididunt ut labore et dolore magna aliqua. <span class="url">https://lorenfield.org</span></p>
  <hr><div class="by"><span class="badge work" aria-label="WorkLoop"></span><div><strong>@vexmoreedu.</strong><small>5 hour ago</small></div></div>
</article>

<div class="abs blog-band"></div>
<h2 class="abs section-title" style="top:1871px">Latest Blog Post</h2>

<div class="abs post-img" style="left:107px;background:linear-gradient(135deg,#d9a7c2,#b86f8e 45%,#e0c070)" role="img" aria-label="Photograph of a teacher reading with a group of young children"></div>
<div class="abs date" style="left:259px"><span>Jan</span><b>23</b></div>
<article class="abs post" style="left:338px">
  <h4>Lorem Ipsum Dolor It Amet Consectetur Elit Sed.</h4>
  <p>Lorem ipsum dolor sit amet consec tetur adipiscing elitfr sed do eiusmod tempor incididunt ut...</p>
  <a>Read More &#x2794;</a>
</article>

<div class="abs post-img" style="left:620px;background:linear-gradient(135deg,#e6ddd0,#c7b39a 50%,#8fae6a)" role="img" aria-label="Photograph of two pupils smiling at a classroom desk"></div>
<div class="abs date" style="left:772px"><span>Jan</span><b>23</b></div>
<article class="abs post" style="left:851px">
  <h4>Lorem Ipsum Dolor It Amet Consectetur Elit Sed.</h4>
  <p>Lorem ipsum dolor sit amet consec tetur adipiscing elitfr sed do eiusmod tempor incididunt ut...</p>
  <a>Read More &#x2794;</a>
</article>

<footer class="abs footer">
  <div class="abs addr">Mr. Alan Brisco, 17 Wexbury Lane,<br>Dunmere, Kestshire, CO14 8PN.</div>
  <div class="abs socials"><span><i></i>Plazora</span><span><i></i>chirpnet</span></div>
  <div class="abs copy">Copyrights © 2019 Vexmore Education.<br>All Rights Reserved</div>
</footer>

</body>
</html>
```